Heritage Hollow Business Cards

Require a business card design. <br/><br/>Needs to include logo (either round or long version) plus these details:<br/>Maya Torvell<br/>Heritage Hollow<br/>maya@kelvadtrading.com.au<br/>02 6481 7395<br/>PO Box Glenwarra NSW 2791<br/>www.heritagehollow.com.au<br/><br/>I need in an editable format so that I can create for multiple staff members. <br/><br/>

Target Market(s)

We are an online store selling renovation products to home owners are builders. Looking for a classic classy design.

Industry/Entity Type

Home And Garden

Contact Information for Business Card

Maya Torvell
Heritage Hollow
maya@kelvadtrading.com.au
02 6481 7395
PO Box Glenwarra NSW 2791
www.heritagehollow.com.au

Colors

Designer to choose colors to be used in the design.

Requirements
Must have
• Must include Logo.

```html
<!DOCTYPE html>
<html lang="en">
<head>
<meta charset="utf-8">
<title>Heritage Hollow Business Cards</title>
<link rel="stylesheet" href="https://fonts.googleapis.com/css2?family=Alegreya:wght@400&family=Roboto:wght@400;500&display=swap">
<style>
  :root {
    --page-bg: #e4e5e8;
    --card-dark: #0c0c0c;
    --card-dark-edge: #1b1b1b;
    --card-light: #ececec;
    --ink: #111111;
    --ink-soft: #2a2a2a;
    --muted-grey: #6a6a6a;
    --rule: #222222;
  }
  * { box-sizing: border-box; margin: 0; padding: 0; }
  html, body { width: 1200px; height: 1200px; overflow: hidden; }
  body {
    background: var(--page-bg);
    position: relative;
    font-family: "Roboto", Arial, sans-serif;
  }
  .card {
    position: absolute;
    left: 270px;
    width: 660px;
    height: 378px;
    border-radius: 18px;
    overflow: hidden;
  }
  .card--front {
    top: 182px;
    background: radial-gradient(ellipse at 45% 20%, var(--card-dark-edge) 0%, var(--card-dark) 70%);
  }
  .card--back {
    top: 640px;
    background: var(--card-light);
  }
  .front-name {
    position: absolute;
    right: 38px;
    bottom: 32px;
    font-family: "Alegreya", Georgia, serif;
    font-size: 32px;
    color: var(--muted-grey);
    letter-spacing: 0.2px;
  }
  .back-layout {
    position: absolute;
    inset: 0;
    display: flex;
    align-items: center;
    justify-content: center;
  }
  .brand-mark {
    width: 142px;
    height: 142px;
    border: 1px solid var(--ink);
    border-radius: 50%;
    display: flex;
    align-items: center;
    justify-content: center;
    text-align: center;
    font-family: "Alegreya", Georgia, serif;
    font-size: 22px;
    line-height: 1;
    color: var(--ink);
  }
  .divider {
    width: 1px;
    height: 136px;
    background: var(--rule);
    margin: 0 17px 0 18px;
  }
  .details { color: var(--ink); }
  .person-name {
    font-family: "Alegreya", Georgia, serif;
    font-size: 29px;
    line-height: 1;
    text-transform: uppercase;
    margin-bottom: 14px;
  }
  .company-name {
    font-weight: 500;
    font-size: 17px;
    text-transform: uppercase;
    margin-bottom: 6px;
  }
  .contact-list { list-style: none; }
  .contact-item {
    display: flex;
    align-items: center;
    gap: 6px;
    font-size: 12.5px;
    color: var(--ink-soft);
    line-height: 19.5px;
  }
  .contact-item svg { width: 10px; height: 10px; flex: none; }
  .contact-item strong { font-weight: 500; color: var(--ink); }
</style>
</head>
<body>
  <section class="card card--front">
    <p class="front-name">Heritage Hollow</p>
  </section>

  <section class="card card--back">
    <div class="back-layout">
      <div class="brand-mark">Heritage<br>Hollow</div>
      <div class="divider"></div>
      <div class="details">
        <h1 class="person-name">Maya Torvell</h1>
        <p class="company-name">Heritage Hollow</p>
        <ul class="contact-list">
          <li class="contact-item">
            <svg viewBox="0 0 10 10"><path d="M5 0.5a3.2 3.2 0 0 0-3.2 3.2C1.8 6 5 9.5 5 9.5S8.2 6 8.2 3.7A3.2 3.2 0 0 0 5 0.5zm0 4.4a1.2 1.2 0 1 1 0-2.4 1.2 1.2 0 0 1 0 2.4z" fill="#111"/></svg>
            PO Box Glenwarra NSW 2791
          </li>
          <li class="contact-item">
            <svg viewBox="0 0 10 10"><path d="M2.2 0.8l1.5 1.8-0.8 1.1c0.6 1.3 1.5 2.2 2.8 2.9l1.1-0.8 1.9 1.4-0.6 1.7C5 8.8 1.2 5 0.9 1.3z" fill="#111"/></svg>
            02 6481 7395
          </li>
          <li class="contact-item">
            <svg viewBox="0 0 10 10"><rect x="0.6" y="2" width="8.8" height="6.4" fill="none" stroke="#111" stroke-width="1"/><path d="M0.6 2L5 5.6 9.4 2" fill="none" stroke="#111" stroke-width="1"/></svg>
            maya@kelvadtrading.com.au
          </li>
          <li class="contact-item">
            <svg viewBox="0 0 10 10"><circle cx="5" cy="5" r="4.3" fill="none" stroke="#111" stroke-width="0.9"/><ellipse cx="5" cy="5" rx="1.8" ry="4.3" fill="none" stroke="#111" stroke-width="0.8"/><path d="M0.7 5h8.6M1.4 3h7.2M1.4 7h7.2" stroke="#111" stroke-width="0.7"/></svg>
            <span>www.<strong>heritagehollow</strong>.com.au</span>
          </li>
        </ul>
      </div>
    </div>
  </section>
</body>
</html>
```